Book cover for book about Climate Change

Looking for a clean, bold, and attractive cover for a mass-market paperback (5.5"x 8.5") about solving the climate change problem. Title is either "Where the Rivers Meet” or A Harbor Made of Glass” (your choice), subtitle is "A practical field guide to mending the weather — so that the young ones after us inherit steady seasons and open skies," author is Lorne Whitcombe. Thinking that it *might* feature an image of Earth (or a portion thereof) and its very thin layer of atmosphere -- but STRONGLY encourage other ideas too!

Requirements
Nice to have
• Keep it positive — NOT scary doom-and-gloom

```html
<!DOCTYPE html>
<html lang="en">
<head>
<meta charset="utf-8">
<title>A Harbor Made of Glass — Book Cover</title>
<link rel="stylesheet" href="https://fonts.googleapis.com/css2?family=Saira+Extra+Condensed:wght@600;700&family=Montserrat:wght@600;700&display=swap">
<style>
  :root {
    --ink: #1c1c1c;
    --blue: #0e5ca8;
    --cover: #e5e5e5;
    --glow: #ffffff;
    --stage-top: #ffffff;
    --stage-bottom: #979797;
  }
  html, body {
    margin: 0;
    padding: 0;
    width: 1200px;
    height: 1200px;
    overflow: hidden;
  }
  body {
    background: linear-gradient(to bottom, var(--stage-top) 0%, var(--stage-top) 48%, var(--stage-bottom) 100%);
  }
  .cover-art {
    display: block;
    width: 1200px;
    height: 1200px;
  }
  .title {
    font-family: "Saira Extra Condensed", "Arial Narrow", sans-serif;
    font-weight: 700;
  }
  .title--top { fill: var(--ink); }
  .title--bottom { fill: var(--blue); }
  .subtitle {
    font-family: "Montserrat", Arial, sans-serif;
    font-weight: 700;
    font-size: 24px;
    fill: var(--ink);
  }
  .subtitle .accent { fill: var(--blue); }
  .ruler-tick { stroke: var(--blue); stroke-width: 2; }
  .ruler-number {
    font-family: "Montserrat", Arial, sans-serif;
    font-weight: 600;
    font-size: 33px;
    fill: var(--blue);
  }
  .author {
    font-family: "Saira Extra Condensed", "Arial Narrow", sans-serif;
    font-weight: 700;
    fill: var(--blue);
  }
</style>
</head>
<body>
<svg class="cover-art" viewBox="0 0 1200 1200" xmlns="http://www.w3.org/2000/svg">
  <defs>
    <radialGradient id="cover-glow" cx="430" cy="640" r="360" gradientUnits="userSpaceOnUse">
      <stop offset="0" stop-color="#ffffff"/>
      <stop offset="1" stop-color="#e5e5e5"/>
    </radialGradient>
    <radialGradient id="planet-tones" cx="0.42" cy="0.45" r="0.7">
      <stop offset="0" stop-color="#e9ecef"/>
      <stop offset="0.35" stop-color="#8a99b5"/>
      <stop offset="0.7" stop-color="#2f3f6f"/>
      <stop offset="1" stop-color="#1b2550"/>
    </radialGradient>
    <linearGradient id="planet-land" x1="0" y1="0" x2="0" y2="1">
      <stop offset="0" stop-color="#b07a45" stop-opacity="0.55"/>
      <stop offset="0.3" stop-color="#b07a45" stop-opacity="0"/>
    </linearGradient>
  </defs>

  <rect class="cover-panel" x="182" y="29" width="835" height="1141" fill="url(#cover-glow)"/>

  <text class="title title--top" x="229" y="260" font-size="240" textLength="743" lengthAdjust="spacingAndGlyphs">A HARBOR</text>
  <text class="title title--bottom" x="247" y="395" font-size="168" textLength="725" lengthAdjust="spacingAndGlyphs">MADE OF GLASS</text>

  <g class="subtitle">
    <text x="229" y="500" textLength="339" lengthAdjust="spacing"><tspan class="accent">A PRACTICAL</tspan> FIELD</text>
    <text x="229" y="537" textLength="339" lengthAdjust="spacing">GUIDE TO MENDING THE</text>
    <text x="229" y="574" textLength="339" lengthAdjust="spacing">WEATHER — SO THAT THE</text>
    <text x="229" y="611" textLength="339" lengthAdjust="spacing">YOUNG ONES AFTER US</text>
    <text x="229" y="648" textLength="339" lengthAdjust="spacing">INHERIT STEADY SEASONS</text>
    <text x="229" y="685" textLength="339" lengthAdjust="spacing">AND OPEN SKIES</text>
  </g>

  <g class="ruler">
    <line class="ruler-tick" x1="751" y1="483" x2="823" y2="483"/>
    <line class="ruler-tick" x1="751" y1="494.5" x2="806" y2="494.5"/>
    <line class="ruler-tick" x1="751" y1="506" x2="806" y2="506"/>
    <line class="ruler-tick" x1="751" y1="517.5" x2="806" y2="517.5"/>
    <line class="ruler-tick" x1="751" y1="529" x2="823" y2="529"/>
    <line class="ruler-tick" x1="751" y1="540.5" x2="806" y2="540.5"/>
    <line class="ruler-tick" x1="751" y1="552" x2="806" y2="552"/>
    <line class="ruler-tick" x1="751" y1="563.5" x2="806" y2="563.5"/>
    <line class="ruler-tick" x1="751" y1="575" x2="823" y2="575"/>
    <line class="ruler-tick" x1="751" y1="586.5" x2="806" y2="586.5"/>
    <line class="ruler-tick" x1="751" y1="598" x2="806" y2="598"/>
    <line class="ruler-tick" x1="751" y1="609.5" x2="806" y2="609.5"/>
    <line class="ruler-tick" x1="751" y1="621" x2="823" y2="621"/>
    <line class="ruler-tick" x1="751" y1="632.5" x2="806" y2="632.5"/>
    <line class="ruler-tick" x1="751" y1="644" x2="806" y2="644"/>
    <line class="ruler-tick" x1="751" y1="655.5" x2="806" y2="655.5"/>
    <line class="ruler-tick" x1="751" y1="667" x2="823" y2="667"/>
    <line class="ruler-tick" x1="751" y1="678.5" x2="806" y2="678.5"/>

    <line class="ruler-tick" x1="751" y1="1007" x2="806" y2="1007"/>
    <line class="ruler-tick" x1="751" y1="1018.5" x2="806" y2="1018.5"/>
    <line class="ruler-tick" x1="751" y1="1030" x2="823" y2="1030"/>
    <line class="ruler-tick" x1="751" y1="1041.5" x2="806" y2="1041.5"/>
    <line class="ruler-tick" x1="751" y1="1053" x2="806" y2="1053"/>
    <line class="ruler-tick" x1="751" y1="1064.5" x2="806" y2="1064.5"/>
    <line class="ruler-tick" x1="751" y1="1076" x2="806" y2="1076"/>
    <line class="ruler-tick" x1="751" y1="1087.5" x2="823" y2="1087.5"/>
    <line class="ruler-tick" x1="751" y1="1099" x2="806" y2="1099"/>
    <line class="ruler-tick" x1="751" y1="1110.5" x2="806" y2="1110.5"/>
    <line class="ruler-tick" x1="751" y1="1122" x2="806" y2="1122"/>
    <line class="ruler-tick" x1="751" y1="1133.5" x2="806" y2="1133.5"/>
    <line class="ruler-tick" x1="751" y1="1145" x2="823" y2="1145"/>
    <line class="ruler-tick" x1="751" y1="1156.5" x2="806" y2="1156.5"/>

    <text class="ruler-number" x="833" y="495">1</text>
    <text class="ruler-number" x="831" y="541">2</text>
    <text class="ruler-number" x="831" y="587">3</text>
    <text class="ruler-number" x="831" y="633">4</text>
    <text class="ruler-number" x="831" y="679">5</text>
  </g>

  <g role="img" aria-label="Photograph of planet Earth seen from space, with cloud swirls over blue oceans and desert land">
    <circle cx="773" cy="840" r="163" fill="url(#planet-tones)"/>
    <circle cx="773" cy="840" r="163" fill="url(#planet-land)"/>
  </g>

  <text class="author" x="229" y="1140" font-size="100" textLength="470" lengthAdjust="spacingAndGlyphs">LORNE WHITCOMBE</text>
</svg>
</body>
</html>
```